KVB Website

We need a website for a company based in Doha Qatar called Brightpath Talent Global. It is a global recruitment company, that specializes in both mass recruitment and headhunting. The company is the number 1 one stop shop for recruitment in Qatar. It recruits from all over the world Europe, Asia, Americas, Middle East, Africa for Qatar.

Target Market(s)

Multinational companies, fortune 500 company CEO's, any top earning companies that are looking for a large number of employees or headhunting employees.
Also for candidates looking for companies to work in Qatar.

Industry/Entity Type

Shop

Colors
ffffff

Requirements
Must have
• Most important qualities the website needs to have:
Clean
Modern
Elegant
Professional
Less Tabs
Minimalisitc

Some examples, I would like you to follow are here:
http://www.velmora.ca/
http://www.trovenkip.com/
https://quelbrandix.com/match#

The main color should be white and it has to have a very stylish, modern and cool look. While being minimalistic. I do not want too many tabs. I want it to be simplistic to understand. the only place where the pink logo color is should be in the logo. The logo color should not be anywhere else. It has to be absolutely sleek. Please follow the example websites that I have provided.

I will send the contact details you need to add later. There is no need for a log in page.

Whatever you think that may be important for a recruitment site do suggest. But there is no need for a log in area as we are a different kind of recruitment company.

There should be an area for testimonials from clients. There should also be an area for news flash for the latest countries we are hiring from and the latest companies we are hiring for and the latest positions we are looking for.

Show me the best please. Whoever gives me the best, I will give them an order for the 2nd website too.

Nice to have
• I have included a powerpoint to explain more!

```html
<!DOCTYPE html>
<html lang="en">
<head>
<meta charset="utf-8">
<title>Brightpath Talent Global — Contact</title>
<link rel="stylesheet" href="https://fonts.googleapis.com/css2?family=Roboto+Slab:wght@300;400;700&display=swap">
<style>
  :root {
    --white: #ffffff;
    --ink: #000000;
    --panel: #eaeaea;
    --rule: #d6d6d6;
    --brand: #9c2a66;
    --placeholder: #dedede;
  }
  * { box-sizing: border-box; margin: 0; padding: 0; }
  html, body { width: 1200px; height: 900px; overflow: hidden; background: var(--white); }
  body { position: relative; font-family: "Roboto Slab", Georgia, serif; color: var(--ink); }

  .site-header {
    position: absolute; left: 0; top: 0; width: 1200px; height: 128px;
    border-top: 2px dotted var(--rule);
    border-bottom: 2px dotted var(--rule);
    box-shadow: 0 3px 4px rgba(0,0,0,0.08);
    background: var(--white);
  }
  .brand { position: absolute; left: 125px; top: 40px; display: flex; align-items: center; gap: 10px; }
  .brand-dot { width: 30px; height: 30px; border-radius: 50%; background: var(--brand); }
  .brand-name { font-weight: 700; font-size: 19px; line-height: 22px; color: var(--brand); width: 200px; }

  .social-link {
    position: absolute; left: 621px; top: 24px; width: 44px; height: 44px;
    display: flex; align-items: center; justify-content: center;
    font-size: 11px; font-weight: 400; color: var(--ink); text-decoration: none;
    border: 1px solid var(--ink); border-radius: 4px;
  }
  .signup-field {
    position: absolute; left: 685px; top: 27px; width: 255px; height: 35px;
    border: 1px dashed var(--ink); border-radius: 18px;
    font: 300 18px "Roboto Slab", Georgia, serif; color: var(--ink);
    padding-left: 21px; display: flex; align-items: center; white-space: nowrap;
  }
  .signup-button {
    position: absolute; left: 952px; top: 27px; width: 120px; height: 35px;
    background: var(--ink); color: var(--white); border-radius: 10px;
    font-size: 23px; font-weight: 400; display: flex; align-items: center; justify-content: center;
  }
  .main-nav a {
    position: absolute; top: 90px; font-weight: 700; font-size: 17px;
    color: var(--ink); text-decoration: none; transform: translateX(-50%); white-space: nowrap;
  }
  .main-nav .is-active::after {
    content: ""; position: absolute; left: 1px; right: -1px; top: 30px; height: 6px; background: var(--ink);
  }

  .form-title { position: absolute; top: 198px; font-size: 23px; font-weight: 400; text-transform: uppercase; white-space: nowrap; }
  .contact-form { position: absolute; top: 235px; width: 446px; height: 531px; background: var(--panel); }
  .field-label { position: absolute; font-size: 16px; text-align: right; white-space: nowrap; }
  .field-input { position: absolute; left: 170px; width: 251px; height: 31px; background: var(--white); }
  .field-area { position: absolute; left: 170px; top: 141px; width: 251px; height: 314px; background: var(--white); }
  .send-button {
    position: absolute; left: 342px; top: 477px; width: 78px; height: 31px; background: var(--white);
    font-size: 23px; font-weight: 700; display: flex; align-items: center; justify-content: center;
  }

  .map-area {
    position: absolute; left: 124px; top: 850px; width: 446px; height: 60px;
    background: var(--placeholder);
  }
  .location-panel { position: absolute; left: 626px; top: 850px; width: 446px; height: 60px; background: var(--panel); }
  .location-title { position: absolute; left: 28px; top: 17px; font-size: 23px; font-weight: 700; }
</style>
</head>
<body>
  <header class="site-header">
    <div class="brand"><span class="brand-dot"></span><span class="brand-name">Brightpath Talent Global</span></div>
    <a class="social-link" href="#">Folkly</a>
    <div class="signup-field">enter your e-mail address</div>
    <div class="signup-button">SIGN UP</div>
    <nav class="main-nav">
      <a href="#" style="left:549px">Home</a>
      <a href="#" style="left:688px">Latest news</a>
      <a href="#" style="left:819px">Clients</a>
      <a href="#" style="left:929px">About</a>
      <a href="#" class="is-active" style="left:1035px">Contact</a>
    </nav>
  </header>

  <h2 class="form-title" style="left:126px">Employers contact</h2>
  <section class="contact-form" style="left:124px">
    <span class="field-label" style="top:37px;right:280px">Company name:</span>
    <div class="field-input" style="top:34px"></div>
    <span class="field-label" style="top:91px;right:280px">Title:</span>
    <div class="field-input" style="top:87px"></div>
    <span class="field-label" style="top:137px;right:279px">Description:</span>
    <div class="field-area"></div>
    <div class="send-button">SEND</div>
  </section>

  <h2 class="form-title" style="left:626px">Workers contact</h2>
  <section class="contact-form" style="left:626px">
    <span class="field-label" style="top:37px;right:281px">Full name:</span>
    <div class="field-input" style="top:34px"></div>
    <span class="field-label" style="top:90px;right:279px">Position:</span>
    <div class="field-input" style="top:87px"></div>
    <span class="field-label" style="top:137px;right:278px">Description:</span>
    <div class="field-area"></div>
    <div class="send-button">SEND</div>
  </section>

  <div class="map-area" role="img" aria-label="Map showing the office location"></div>
  <section class="location-panel"><h2 class="location-title">LOCATION</h2></section>
</body>
</html>
```